Corvell Tea range - labels for a range of teas.

Our company name is Corvell Tea Company - based in Melbourne, Australia. We have a current logo project with Pavlo Grid.

We offer a range of top quality teas - black, green, white, oolongs, herbals, flavoured teas. From Japan, Assam, Darjeeling, Ceylon, Africa and elsewhere. The very best loose teas, and some pyramid tea bags too.

We cover some blends : English Breakfast, African Breakfast, Ceylon Breakfast, Earl Grey amongst them.

And herbal variants: lemon grass and ginger, chamomile, peppermint, rooibos and chilli.

And fruit teas.... and flavoured teas like vanilla, peach and raspberry.

We aim to occupy a modern, contemporary, sophisticated and global space.... but we can be funky too, especially with the fruit and herbal offers. Quality is paramount ! We do not aim to have the biggest range of teas, but we are very particular. And we source directly from origin.... fresh quality teas.

Would lean towards black teas being on a black background label, green teas on a green background, white etas on a white background, herbals maybe on a straw or suitable background, and flavoured teas on a specific background colour too....maybe fuschia? Violet ? But colourful is key.

The panel should indicate teas being Loose or Pyramid bags. And the nett weight should be shown.... Loose could be for example 75 gr, 125 gr 250 gr etc.. And pyramids would show the number of pyramids and weight, example 20 x Pyramids 50 gr
50 Pyramids 150 gr etc.

And 'Corvell Teas' or 'Corvell Tea Company' should be on the panel too. Melbourne can appear as well if it gels with the total look.

There will need to be 2 lines - in order or juxtaposed, doesn't matter - showing the origin and 'mark' and grade. Example being:
Ceylon
Wendrith Pekoe

or

Darjeeling
Kalmore TGFOP1

or

China
Jasmine Leaf

We just need templates to cover the different types of tea - black, green, white, herbal, flavoured - as there are too many (and changing) types of tea in the range .

Any questions...please ask...

Thanks

Reason: Needs to have alater deadline than the current Logo Project associated with the same Corvell Tea Company start up.

Target Market(s)

Sophisticated. Real tea lovers. Discriminating tastes.

Industry/Entity Type

Weight

Font styles to use
Sans Serif

Requirements
Must have
• Sophisticated
Cool
Premium quality branding
Bold
Uber modern
Nice to have
• BOLD text.....
Cool fonts....
Pretty bold and minimalist - ultra modern if possible....uber modern
Bright colours and use of black and white..... Not really into pastels etc..

Lots of black colour too is a likely plus
Should not have
• Frilly stuff

```html
<!DOCTYPE html>
<html lang="en">
<head>
<meta charset="utf-8">
<title>Corvell Tea – label range</title>
<link rel="stylesheet" href="https://fonts.googleapis.com/css2?family=Arimo:wght@400;700&display=swap">
<style>
  :root {
    --page: #ffffff;
    --label-bg: #3a3a3c;
    --title: #b5b5b7;
    --ink-light: #ffffff;
    --ink-herbal: #8c8c8f;
    --black-tea: #bdbec0;
    --white-tea: #ffffff;
    --green-tea: #8dc63f;
    --herbal-tea: #f2eb35;
    --flavoured-tea: #f15a29;
    --oolong-tea: #c3b69c;
  }
  html, body {
    margin: 0;
    padding: 0;
    width: 1200px;
    height: 848px;
    overflow: hidden;
    background: var(--page);
  }
  .range {
    position: relative;
    width: 1200px;
    height: 848px;
    font-family: "Arimo", Arial, sans-serif;
  }
  .label {
    position: absolute;
    width: 202px;
    height: 284px;
    display: block;
    overflow: hidden;
  }
  .label-bg { fill: var(--label-bg); }
  .tea-title {
    fill: var(--title);
    font-weight: 700;
    font-size: 48px;
    letter-spacing: -2.5px;
  }
  .tea-title.is-long { font-size: 36px; letter-spacing: -1.5px; }
  .origin { fill: var(--ink-light); font-weight: 700; font-size: 27px; letter-spacing: -1px; }
  .grade { fill: var(--ink-light); font-weight: 400; font-size: 15px; letter-spacing: -0.2px; }
  .origin.is-herbal, .grade.is-herbal {
    fill: var(--ink-herbal);
    font-weight: 700;
    font-size: 22px;
    letter-spacing: -0.8px;
  }
  .brand { fill: var(--ink-light); font-weight: 700; font-size: 11px; }
  .weight { fill: var(--ink-light); font-weight: 700; font-size: 12px; }
  .cup-black { fill: var(--black-tea); }
  .cup-white { fill: var(--white-tea); }
  .cup-green { fill: var(--green-tea); }
  .cup-herbal { fill: var(--herbal-tea); }
  .cup-flavoured { fill: var(--flavoured-tea); }
  .cup-oolong { fill: var(--oolong-tea); }
</style>
</head>
<body>
<main class="range">

  <svg class="label" style="left:51px;top:40px" viewBox="0 0 202 284" aria-label="Black tea label">
    <rect class="label-bg" width="202" height="284"/>
    <g class="cup-black"><circle cx="167" cy="152" r="74"/><path d="M112 200 Q100 216 94 226 Q90 236 100 234 Q112 228 126 214 Z"/></g>
    <g transform="translate(26 112) rotate(-40)">
      <text class="tea-title">Black</text>
      <text class="tea-title" x="34" y="38">TEA</text>
    </g>
    <text class="origin" x="46" y="170">Darjeeling</text>
    <text class="grade" x="57" y="192">Kalmore TGFOP1</text>
    <text class="brand" x="60" y="262">Corvell Tea</text>
    <text class="weight" x="192" y="275" text-anchor="end">125g</text>
  </svg>

  <svg class="label" style="left:299px;top:40px" viewBox="0 0 202 284" aria-label="White tea label">
    <rect class="label-bg" width="202" height="284"/>
    <g class="cup-white"><circle cx="167" cy="152" r="74"/><path d="M112 200 Q100 216 94 226 Q90 236 100 234 Q112 228 126 214 Z"/></g>
    <g transform="translate(26 112) rotate(-40)">
      <text class="tea-title">White</text>
      <text class="tea-title" x="34" y="38">TEA</text>
    </g>
    <text class="brand" x="60" y="262">Corvell Tea</text>
    <text class="weight" x="192" y="275" text-anchor="end">125g</text>
  </svg>

  <svg class="label" style="left:548px;top:40px" viewBox="0 0 202 284" aria-label="Green tea label">
    <rect class="label-bg" width="202" height="284"/>
    <g class="cup-green"><circle cx="167" cy="152" r="74"/><path d="M112 200 Q100 216 94 226 Q90 236 100 234 Q112 228 126 214 Z"/></g>
    <g transform="translate(26 112) rotate(-40)">
      <text class="tea-title">Green</text>
      <text class="tea-title" x="34" y="38">TEA</text>
    </g>
    <text class="brand" x="60" y="262">Corvell Tea</text>
    <text class="weight" x="192" y="275" text-anchor="end">125g</text>
  </svg>

  <svg class="label" style="left:793px;top:40px" viewBox="0 0 202 284" aria-label="Herbal tea label">
    <rect class="label-bg" width="202" height="284"/>
    <g class="cup-herbal"><circle cx="167" cy="152" r="74"/><path d="M112 200 Q100 216 94 226 Q90 236 100 234 Q112 228 126 214 Z"/></g>
    <g transform="translate(26 112) rotate(-40)">
      <text class="tea-title">Herbal</text>
      <text class="tea-title" x="34" y="38">TEA</text>
    </g>
    <text class="origin is-herbal" x="40" y="164">Lemongrass&amp;</text>
    <text class="grade is-herbal" x="106" y="192">ginger</text>
    <text class="brand" x="60" y="262">Corvell Tea</text>
    <text class="weight" x="192" y="275" text-anchor="end">125g</text>
  </svg>

  <svg class="label" style="left:51px;top:367px" viewBox="0 0 202 284" aria-label="Flavoured tea label">
    <rect class="label-bg" width="202" height="284"/>
    <g class="cup-flavoured"><circle cx="167" cy="152" r="74"/><path d="M112 200 Q100 216 94 226 Q90 236 100 234 Q112 228 126 214 Z"/></g>
    <g transform="translate(22 140) rotate(-40)">
      <text class="tea-title is-long">Flavoured</text>
      <text class="tea-title" x="67" y="35">TEA</text>
    </g>
    <text class="brand" x="60" y="262">Corvell Tea</text>
    <text class="weight" x="192" y="275" text-anchor="end">125g</text>
  </svg>

  <svg class="label" style="left:299px;top:367px" viewBox="0 0 202 284" aria-label="Oolong tea label">
    <rect class="label-bg" width="202" height="284"/>
    <g class="cup-oolong"><circle cx="167" cy="152" r="74"/><path d="M112 200 Q100 216 94 226 Q90 236 100 234 Q112 228 126 214 Z"/></g>
    <g transform="translate(26 120) rotate(-40)">
      <text class="tea-title">Oolong</text>
      <text class="tea-title" x="34" y="38">TEA</text>
    </g>
    <text class="brand" x="60" y="262">Corvell Tea</text>
    <text class="weight" x="192" y="275" text-anchor="end">125g</text>
  </svg>

</main>
</body>
</html>
```